Church Website with Home Page and Member Sermon Library

I am in need of an updated design for our church website. This will include 4 pages (outlined below). We are a conservative, evangelical, Christian church. The site should be modern and clean, while still reflecting our conservative values. I already have a logo for our church, and I want the site to incorporate the logo, and match the logo/branding. Stock photos are allowed if needed, but I have uploaded some images of our church and would prefer those images to be used if possible. Any stock photos used should not include any people in the photos (scenery, nature, buildings, animals, etc. are fine).

The site will need 4 pages: Home, Support Us (Donate), Login, and Recording Library.

Page 1: Home
The home page should include the following sections:

- Navigation: Should include links to each section of the home page plus a "listen live" link which will take the user to a live-streaming site and a "support us" link which will take the user to a support/donate page.

- Announcements: Can be either a banner or some other design, but there needs to be some way for us to post announcements for visitors to see. I'm open for creative ideas in this section, but would like it not to take up a lot of room on the page.

- About Us: Should include address, service times (see attached document), and information about the church.

- Pastor Bio: A section that introduces our pastor and gives a short bio about our pastor. Would like this section to include a picture of our pastor. Somewhere in this section I would like to include this Bible reference: "And I will give you pastors according to mine heart, which shall feed you with knowledge and understanding. Jer 3:15 LPW"

- Articles of Faith (What We Believe): This should include several sub-sections each with a heading, body, and possibly 1 or more scripture references. I have attached a document to the brief that includes our articles of faith. Feel free to be creative with this section in how you lay these out and format them.

- Support Us: A small section that explains what kind of support someone can give and a link to a donation page. The link can say something like "Support Us" or "Donate Now".

- Contact form: A contact form that allows the visitor to send us a message. The contact form should ask for name, email, phone, and message.

- Footer: A footer that will be displayed on all pages of the site. This should include at a minimum a link to the home page (or a link to each individual section in the home page if you prefer), a link to "listen live", a link to "support us", a link to "contact us" (or you can put the contact form directly in the footer if you prefer), the address, and a "member login" link.

Page 2: Support Us
The donation page should include a form the visitor can fill out to make a donation. We will embed a third party form later. For this design, please just mock out the design with a basic form asking for name, phone, and email.

Page 3: Login
The recording library (detailed below) will require members to login with a shared numeric code before accessing the page. We need a design for a login screen. The screen should include navigation/footer just like all other pages, but the body of the login page will consist only of a form that asks the user to enter the access code and then a "login" button.

Page 4: Recording Library

The library page is a member-only page that will require a shared, numeric pass code to access. On this page, members will be able to access a filterable list of past sermons. The page by default should display most recent sermons, but should also include a search form that allows the member to filter the sermon list to find a particular sermon. The search form should allow the user to select a filter type (e.g. Speaker name, date, event, etc.) and type in a value to search. They should be able to add multiple filters and remove filters that have been added. Each sermon that is displayed in the result list should include basic information such as title, date, speaker, tags, etc. along with a download icon, and an embedded audio player where they can click a play button to stream it on-demand. Each sermon should also have clickable tags associated with it that can be used to find related sermons.
Updates

I have uploaded several images of our church. Feel free to incorporate these into your design if possible.

Target Market(s)

Church Members

Industry/Entity Type

Religion

Number of Pages Required

4 page

Font styles to use
Sans Serif

Colors

Designer to choose colors to be used in the design.

Requirements
Must have
• Must incorporate the logo (attached)
Nice to have
• Would like the design to incorporate pictures of our church (attached) instead of stock photos if possible.
Should not have
• Please avoid an overly cluttered design. Stock photos used should not include any people in the photos.

```html
<!DOCTYPE html>
<html lang="en">
<head>
<meta charset="utf-8">
<title>Grace Harbor Church – Website Pages</title>
<link href="https://fonts.googleapis.com/css2?family=Poppins:wght@300;400;500;600;700;800&family=Great+Vibes&display=swap" rel="stylesheet">
<style>
:root{
  --board:#bccfd6;
  --ink:#1d1b1a;
  --footer:#231f1c;
  --teal:#1fb8c9;
  --green:#8fcf5a;
  --pink:#ef4a5e;
  --pink-soft:#f7a3ae;
  --field:#e4e4e4;
  --muted:#8a8a8a;
  --white:#ffffff;
  --brand:#2a9fb3;
}
*{box-sizing:border-box;margin:0;padding:0}
html,body{width:1200px;height:808px;overflow:hidden}
body{background:var(--board);font-family:"Poppins",sans-serif;color:var(--ink);position:relative}
a{color:inherit;text-decoration:none}
.page{position:absolute;background:var(--white);overflow:hidden;box-shadow:0 4px 10px rgba(0,0,0,.18)}
.abs{position:absolute}

/* brand */
.brand{position:absolute;display:flex;align-items:center;gap:3px;color:var(--brand);font-weight:500;letter-spacing:.04em;white-space:nowrap}
.brand-mark{width:1em;height:1em;border:1px solid var(--brand);display:block}

/* footer */
.site-footer{position:absolute;left:0;right:0;bottom:0;background:var(--footer);color:var(--white);font-size:6.5px}
.foot{position:absolute}
.foot .col{position:absolute;top:0;white-space:nowrap}
.foot .c2{left:9.8em}.foot .c3{left:17em}.foot .c4{left:26em}
.foot h4{font-weight:700;line-height:1em;margin-bottom:1.5em;font-size:1em}
.foot .col a{display:block;line-height:1em;margin-bottom:1.4em;font-weight:300}
.foot p{line-height:1.19em;font-weight:300}
.foot .write{margin-top:.6em;margin-bottom:0}
.foot .mail{text-decoration:underline;margin-top:1.2em}
.social{display:flex;gap:2.2em;margin-top:.4em}
.social span{width:2em;height:2em;border-radius:50%;background:var(--white);display:block}
.foot .copy{position:absolute;top:17em;left:0;white-space:nowrap;font-weight:300}
.copy a{color:#5aa7ff;text-decoration:underline}
.site-footer--compact{font-size:5.2px}

/* home */
.home{left:29px;top:24px;width:320px;height:760px}
.home-nav{position:absolute;top:0;left:0;right:0;height:20px;background:var(--white);z-index:2}
.home-nav .links{position:absolute;right:21px;top:8px;display:flex;gap:9px;font-size:3.6px;font-weight:600}
.hero-photo{position:absolute;left:96px;top:20px;width:224px;height:106px;background:linear-gradient(90deg,#fff 0%,#f4ece2 25%,#e7d4bd 60%,#d9c0a2 100%)}
.hero-title{left:30px;top:34px;font-size:12.5px;font-weight:800;line-height:17px}
.hero-sub{left:30px;top:72px;font-size:7.2px;font-weight:600}
.hero-text{left:30px;top:84px;width:130px;font-size:5.3px;line-height:7px}
.pill{position:absolute;border-radius:20px;color:var(--white);font-weight:700;display:flex;align-items:center;justify-content:center;white-space:nowrap}
.join{left:30px;top:102px;width:48px;height:14px;background:var(--teal);font-size:5.8px}
.welcome-title{left:54px;top:138px;font-family:"Great Vibes",cursive;font-size:15px}
.welcome-text{left:60px;top:172px;width:206px;font-size:6px;line-height:8px;text-align:justify}
.know{left:60px;top:226px;width:74px;height:15px;background:var(--teal);font-size:4.6px;box-shadow:0 2px 3px rgba(0,0,0,.15)}
.believe{position:absolute;left:0;top:253px;width:320px;height:127px;background:linear-gradient(180deg,#eceae6 0%,#d8d1c8 50%,#c9bdb0 100%)}
.believe-tag{left:0;width:320px;top:265px;text-align:center;font-size:5.8px;font-weight:600}
.believe-title{left:0;width:320px;top:281px;text-align:center;font-size:15px;font-weight:800}
.believe-text{left:40px;width:240px;top:310px;text-align:center;font-size:7.1px;line-height:9.5px}
.dots{left:126px;top:359px;display:flex;gap:5px}
.dots span{width:4px;height:4px;border-radius:50%;background:#f3f1ee}
.dots span:first-child{background:#111}
.pastor-photo{position:absolute;left:38px;top:388px;width:90px;height:119px;background:linear-gradient(180deg,#f4f4f5,#e3e4e7)}
.kicker{left:152px;top:403px;font-size:3.4px;font-weight:600}
.verse-ref{left:152px;top:414px;font-size:10.5px;font-weight:800}
.verse{left:152px;top:434px;width:140px;font-size:7.2px;font-weight:600;line-height:9.7px}
.pastor-text{left:152px;top:473px;width:140px;font-size:6px;line-height:8px}
.service{position:absolute;left:0;top:507px;width:320px;height:127px;background:linear-gradient(180deg,#f1f2f3,#ffffff)}
.svc-title{left:52px;width:100px;top:528px;text-align:center;font-size:7.2px;font-weight:800}
.svc-list{left:52px;width:100px;top:545px;text-align:center;font-size:6.1px;line-height:8.2px}
.svc-list b{font-weight:600}
.ann-title{left:180px;top:526px;font-size:7.2px;font-weight:800;display:flex;align-items:center;gap:3px}
.ann-box{left:167px;top:539px;width:98px;height:74px;border-radius:5px;background:linear-gradient(180deg,#22b9c9,#8fcf5a);color:var(--white);font-size:5.9px;font-weight:700;line-height:8.3px;text-align:center;display:flex;align-items:center;justify-content:center;padding:0 10px}
.donate-pill{left:132px;top:628px;width:56px;height:13px;background:var(--pink);font-size:5px;gap:3px;z-index:3}
.home .site-footer{height:126px}
.home .foot{left:22px;top:22px}

/* donate / login */
.donate{left:370px;top:24px;width:395px;height:370px}
.login{left:370px;top:415px;width:395px;height:369px}
.hero-area{position:absolute;left:0;top:0;width:395px;height:215px}
.donate .hero-area{background:linear-gradient(90deg,#e8cbe0 0%,#ef93a7 35%,#f0576b 60%,#ef4a5e 100%)}
.login .hero-area{height:213px;background:linear-gradient(90deg,#4a3f36 0%,#3a322b 40%,#2b2521 100%)}
.big-title{left:39px;top:28px;font-size:19px;font-weight:800;line-height:25px;color:var(--white);letter-spacing:.01em}
.donate .big-title{color:#fff6f7}
.big-sub{left:39px;width:90px;font-size:7.4px;line-height:9.6px;color:var(--white);font-weight:300}
.card{position:absolute;left:203px;width:186px;background:var(--white);border-radius:4px}
.donate .card{top:6px;height:203px}
.login .card{top:5px;height:203px}
.card .brand{font-size:8px}
.lbl{position:absolute;font-size:4.3px;font-weight:600}
.fld{position:absolute;background:var(--field);border:.5px solid #cfcfcf}
.btn-donate{left:30px;top:172px;width:129px;height:20px;border-radius:2px;background:linear-gradient(90deg,#ef4a5e 30%,#f7b5bd 100%);color:var(--white);font-size:7.5px;font-weight:700;display:flex;align-items:center;justify-content:center}
.btn-login{left:30px;top:120px;width:129px;height:19px;background:linear-gradient(90deg,#1fb8c9,#93d15a);color:var(--ink);font-size:6.5px;font-weight:700;display:flex;align-items:center;justify-content:center}
.terms{left:30px;top:173px;width:129px;font-size:4.1px;line-height:5.6px;color:#666}
.terms u{text-decoration:underline}
.donate .site-footer,.login .site-footer{height:155px}
.donate .foot,.login .foot{left:27px;top:28px}

/* library */
.library{left:781px;top:24px;width:396px;height:503px}
.side{position:absolute;left:0;top:0;width:74px;height:346px;background:var(--white)}
.side .brand{left:15px;top:14px;font-size:5.6px}
.menu{position:absolute;left:12px;font-size:4.3px;font-weight:600;display:flex;align-items:center;gap:4px;white-space:nowrap}
.menu svg{width:6px;height:6px}
.sub{position:absolute;left:27px;font-size:3.8px;white-space:nowrap}
.lib-main{position:absolute;left:74px;top:0;width:322px;height:346px;background:linear-gradient(180deg,#f2f3f2 0%,#e9efe6 10%,#afd98a 28%,#8dd28a 50%,#4cc3b5 78%,#22b9cf 100%)}
.lib-photo{position:absolute;left:74px;top:40px;width:322px;height:60px;background:linear-gradient(180deg,rgba(255,255,255,0),rgba(200,220,180,.35),rgba(255,255,255,0))}
.search{left:91px;top:8px;width:90px;height:17px;background:#f7f7f7;border:.5px solid #e2e2e2;font-size:4.3px;color:#777;padding:6px 5px}
.category{left:181px;top:8px;width:51px;height:17px;background:#f7f7f7;border:.5px solid #e2e2e2;font-size:4.3px;font-weight:600;padding:6px 5px;display:flex;justify-content:space-between}
.search-btn{left:232px;top:8px;width:17px;height:17px;background:#1d1b1a;display:flex;align-items:center;justify-content:center}
.pager{left:361px;top:11px;display:flex;gap:3px}
.pager span{width:9px;height:9px;border-radius:50%;border:.7px solid #222;font-size:5px;display:flex;align-items:center;justify-content:center;line-height:1}
.lib-title{left:96px;top:46px;font-size:13px;font-weight:800;line-height:14px}
.lib-year{left:96px;top:61px;font-size:6px}
.rule{position:absolute;left:88px;width:300px;height:.6px;background:rgba(0,0,0,.25)}
.shelf-name{position:absolute;left:88px;font-size:6px;font-weight:600}
.shelf{position:absolute;left:86px;display:flex;gap:9px}
.sermon{width:42px}
.thumb{height:42px;border-radius:3px;background:#1e1d1c;position:relative;color:#7d7d7d;font-size:6.5px;display:flex;align-items:center;justify-content:center}
.thumb i{position:absolute;right:3px;bottom:2px;color:var(--white);font-style:normal;font-size:4px}
.sermon h5{font-size:4.3px;font-weight:700;margin-top:3px;line-height:5px}
.sermon p{font-size:2.8px;line-height:3.9px;color:#333}
.library .site-footer{height:157px}
.library .foot{left:99px;top:29px}

/* note */
.note{left:811px;top:578px;font-size:29px;line-height:39px;white-space:nowrap;font-weight:300;letter-spacing:-.3px}
.note b{font-weight:800;font-size:29px;letter-spacing:-.6px}
</style>
</head>
<body>

<!-- HOME PAGE -->
<section class="page home">
  <nav class="home-nav">
    <div class="brand" style="left:21px;top:6px;font-size:5.4px"><span class="brand-mark"></span>GRACE HARBOR</div>
    <div class="links"><a>Get Involved</a><a>About Us</a><a>Log in</a></div>
  </nav>
  <div class="hero-photo" role="img" aria-label="Bright church interior with tall arched windows"></div>
  <h1 class="abs hero-title">LOVE GOD<br>&amp; LOVE LIFE!</h1>
  <p class="abs hero-sub">Join our Live Sermons.</p>
  <p class="abs hero-text">Make your day more fulfilling with a variety of sermons from different speakers.</p>
  <a class="pill join">JOIN NOW</a>

  <h2 class="abs welcome-title">Giving You a Warm Welcome!</h2>
  <p class="abs welcome-text">Our mission is helping people find their way back to God. We accomplish this by reaching people far from God, restoring God's dream for the world, and reproducing this mission in others. There are three key relationships that help you develop a growing relationship with Jesus.</p>
  <a class="pill know">KNOW MORE ABOUT US →</a>

  <div class="believe" role="img" aria-label="Soft view of the brick church building exterior"></div>
  <p class="abs believe-tag">WHAT WE BELIEVE</p>
  <h2 class="abs believe-title">THE GOD HEAD</h2>
  <p class="abs believe-text">We believe in the God head bodily, known as the Divine Trinity. This body consist of God the father, Jesus Christ, his only begotten son and the redeemer of the world, and of the Holy Ghost, The third person of the Divine Trinity.</p>
  <div class="abs dots"><span></span><span></span><span></span><span></span><span></span><span></span><span></span></div>

  <div class="pastor-photo" role="img" aria-label="Portrait photo of the church pastor"></div>
  <p class="abs kicker">SOMETHING TO KNOW</p>
  <h3 class="abs verse-ref">Jer 3:15 LPW</h3>
  <p class="abs verse">“And I will give you pastors according to mine heart, which shall feed you with knowledge and understanding.”</p>
  <p class="abs pastor-text">A section that introduces our pastor and gives a short bio about our pastor. Would like this section to include a picture of our pastor.</p>

  <div class="service"></div>
  <h3 class="abs svc-title">TIME OF SERVICE</h3>
  <p class="abs svc-list"><b>Wednesday Evening Service</b><br>7:30 PM<br><b>Sunday School</b><br>10:00 AM<br><b>Sunday Morning Service</b><br>11:00 AM<br><b>Sunday Evening Service</b><br>5:30 PM</p>
  <h3 class="abs ann-title">ANNOUNCEMENT <svg width="6" height="6" viewBox="0 0 10 10"><rect x="1" y="1" width="8" height="6" rx="1" fill="none" stroke="#1d1b1a"/><path d="M3 7 L3 9 L5 7" fill="none" stroke="#1d1b1a"/></svg></h3>
  <div class="abs ann-box">Be reminded that we will be having a Sunday Sermon with Pastor this coming FEBUARY 30, 2023 at 9:00 PM.</div>
  <a class="pill donate-pill"><svg width="6" height="6" viewBox="0 0 10 10"><path d="M5 9 L1 5 A2.2 2.2 0 0 1 5 2 A2.2 2.2 0 0 1 9 5 Z" fill="#fff"/></svg>DONATE NOW</a>

  <footer class="site-footer site-footer--compact">
    <div class="foot">
      <div class="col"><h4>WHO WE ARE</h4><a>About us</a><a>Ministries</a><a>Events</a></div>
      <div class="col c2"><h4>INFO</h4><a>Careers</a><a>Community</a><a>Blog</a><a>Press</a></div>
      <div class="col c3"><h4>HELP</h4><a>Contact us</a><a>FAQ</a><a>Legal &amp; Privacy</a></div>
      <div class="col c4"><h4>FIND US AT</h4><p>(555) 014-2290<br>Maple Ridge Dr, Eastfield, North<br>Carolina(NC), 27410</p><h4 class="write">WRITE TO US</h4><a class="mail">graceharbor@example.org</a><div class="social"><span></span><span></span><span></span><span></span></div></div>
      <p class="copy">© 2021 Cornerstone. All Rights Reserved. <a>Privacy Policy</a></p>
    </div>
  </footer>
</section>

<!-- SUPPORT US PAGE -->
<section class="page donate">
  <div class="hero-area" role="img" aria-label="Open hands holding a soft glowing light"></div>
  <h1 class="abs big-title">YOUR<br>GIVING<br>CHANGES<br>LIVES,<br>FOREVER</h1>
  <p class="abs big-sub" style="top:155px">Thank you for making a difference.</p>
  <form class="card">
    <div class="brand" style="left:32px;top:28px"><span class="brand-mark"></span>GRACE HARBOR</div>
    <span class="lbl" style="left:30px;top:55px">First name</span>
    <span class="lbl" style="left:100px;top:55px">Last name</span>
    <span class="fld" style="left:30px;top:62px;width:58px;height:13px"></span>
    <span class="fld" style="left:100px;top:62px;width:59px;height:13px"></span>
    <span class="lbl" style="left:30px;top:84px">Email address</span>
    <span class="fld" style="left:30px;top:90px;width:129px;height:13px"></span>
    <span class="lbl" style="left:30px;top:111px">Leave us a message</span>
    <span class="fld" style="left:30px;top:116px;width:129px;height:24px"></span>
    <span class="lbl" style="left:77px;top:151px;font-size:5.8px;font-weight:800">AMOUNT:</span>
    <span class="fld" style="left:108px;top:147px;width:51px;height:13px"></span>
    <a class="abs btn-donate">DONATE</a>
  </form>
  <footer class="site-footer">
    <div class="foot">
      <div class="col"><h4>WHO WE ARE</h4><a>About us</a><a>Ministries</a><a>Events</a></div>
      <div class="col c2"><h4>INFO</h4><a>Careers</a><a>Community</a><a>Blog</a><a>Press</a></div>
      <div class="col c3"><h4>HELP</h4><a>Contact us</a><a>FAQ</a><a>Legal &amp; Privacy</a></div>
      <div class="col c4"><h4>FIND US AT</h4><p>(555) 014-2290<br>Maple Ridge Dr, Eastfield, North<br>Carolina(NC), 27410</p><h4 class="write">WRITE TO US</h4><a class="mail">graceharbor@example.org</a><div class="social"><span></span><span></span><span></span><span></span></div></div>
      <p class="copy">© 2021 Cornerstone. All Rights Reserved. <a>Privacy Policy</a></p>
    </div>
  </footer>
</section>

<!-- LOGIN PAGE -->
<section class="page login">
  <div class="hero-area" role="img" aria-label="Footprints in dark sand"></div>
  <h1 class="abs big-title">JOIN OUR<br>RECORDING<br>LIBRARY OF<br>LATEST<br>SERMONS</h1>
  <p class="abs big-sub" style="top:154px;width:120px">Get access to thousands of sermons by different speakers.</p>
  <form class="card">
    <div class="brand" style="left:32px;top:34px"><span class="brand-mark"></span>GRACE HARBOR</div>
    <span class="lbl" style="left:31px;top:74px;font-size:6.2px">Enter numeric code</span>
    <span class="fld" style="left:30px;top:85px;width:129px;height:19px"></span>
    <span class="lbl" style="left:30px;top:109px;font-size:4.8px;font-weight:400;color:var(--muted)">Minimum 6 numeric characters</span>
    <a class="abs btn-login">LOG IN</a>
    <p class="abs terms">By logging in, I confirm that I have read and agree to the Grace Harbor Church <u>Terms of Service</u>, <u>Privacy Policy</u>, and to receive email and updates.</p>
  </form>
  <footer class="site-footer">
    <div class="foot">
      <div class="col"><h4>WHO WE ARE</h4><a>About us</a><a>Ministries</a><a>Events</a></div>
      <div class="col c2"><h4>INFO</h4><a>Careers</a><a>Community</a><a>Blog</a><a>Press</a></div>
      <div class="col c3"><h4>HELP</h4><a>Contact us</a><a>FAQ</a><a>Legal &amp; Privacy</a></div>
      <div class="col c4"><h4>FIND US AT</h4><p>(555) 014-2290<br>Maple Ridge Dr, Eastfield, North<br>Carolina(NC), 27410</p><h4 class="write">WRITE TO US</h4><a class="mail">graceharbor@example.org</a><div class="social"><span></span><span></span><span></span><span></span></div></div>
      <p class="copy">© 2021 Cornerstone. All Rights Reserved. <a>Privacy Policy</a></p>
    </div>
  </footer>
</section>

<!-- RECORDING LIBRARY PAGE -->
<section class="page library">
  <aside class="side">
    <div class="brand"><span class="brand-mark"></span>GRACE HARBOR</div>
    <a class="menu" style="top:42px"><svg viewBox="0 0 10 10"><path d="M1 5 L5 1 L9 5 V9 H6 V6 H4 V9 H1 Z" fill="#1d1b1a"/></svg>Home</a>
    <a class="menu" style="top:57px"><svg viewBox="0 0 10 10"><rect x="1" y="1" width="2" height="8" fill="#1d1b1a"/><rect x="4" y="1" width="2" height="8" fill="none" stroke="#1d1b1a" stroke-width=".8"/><rect x="7" y="2" width="2" height="7" fill="#1d1b1a"/></svg>Library</a>
    <a class="menu" style="top:72px"><svg viewBox="0 0 10 10"><path d="M5 9 L1 5 A2.2 2.2 0 0 1 5 2 A2.2 2.2 0 0 1 9 5 Z" fill="#1d1b1a"/></svg>Favorites</a>
    <a class="menu" style="top:86px;text-decoration:underline"><svg viewBox="0 0 10 10"><circle cx="5" cy="5" r="4.5" fill="#1d1b1a"/><path d="M5 2.5 V7.5 M2.5 5 H7.5" stroke="#fff" stroke-width="1.2"/></svg>Create Playlist</a>
    <span class="sub" style="left:24px;top:98px;font-weight:700;font-size:3.6px">YOUR PLAYLIST</span>
    <span class="sub" style="top:106px;text-decoration:underline">Holy Sermon 2023</span>
    <span class="sub" style="top:114px">Existence</span>
    <span class="sub" style="top:123px">Marriage</span>
    <a class="menu" style="top:167px"><svg viewBox="0 0 10 10"><circle cx="5" cy="5" r="4" fill="none" stroke="#1d1b1a"/><ellipse cx="5" cy="5" rx="1.8" ry="4" fill="none" stroke="#1d1b1a" stroke-width=".7"/><path d="M1 5 H9" stroke="#1d1b1a" stroke-width=".7"/></svg>English</a>
  </aside>
  <div class="lib-main"></div>
  <div class="lib-photo" role="img" aria-label="Faint view of the church building"></div>
  <div class="abs search">Search</div>
  <div class="abs category"><span>Category</span><span>⌄</span></div>
  <div class="abs search-btn"><svg width="8" height="8" viewBox="0 0 10 10"><circle cx="4.2" cy="4.2" r="3" fill="none" stroke="#fff" stroke-width="1.1"/><path d="M6.5 6.5 L9 9" stroke="#fff" stroke-width="1.2"/></svg></div>
  <div class="abs pager"><span>‹</span><span>›</span></div>
  <h1 class="abs lib-title">HOLY SERMONS</h1>
  <p class="abs lib-year">2023</p>
  <div class="rule" style="top:74px"></div>

  <h2 class="shelf-name" style="top:80px">Corinthians</h2>
  <div class="shelf" style="top:93px">
    <div class="sermon"><div class="thumb">PIC<i>+ ♥</i></div><h5>TITLE</h5><p>A very short description.<br>32 mins · Febuary 12</p></div>
    <div class="sermon"><div class="thumb">PIC<i>+ ♥</i></div><h5>TITLE</h5><p>A very short description.<br>32 mins · Febuary 12</p></div>
    <div class="sermon"><div class="thumb">PIC<i>+ ♥</i></div><h5>TITLE</h5><p>A very short description.<br>32 mins · Febuary 12</p></div>
    <div class="sermon"><div class="thumb">PIC<i>+ ♥</i></div><h5>TITLE</h5><p>A very short description.<br>32 mins · Febuary 12</p></div>
    <div class="sermon"><div class="thumb">PIC<i>+ ♥</i></div><h5>TITLE</h5><p>A very short description.<br>32 mins · Febuary 12</p></div>
    <div class="sermon"><div class="thumb">PIC<i>+ ♥</i></div><h5>TITLE</h5><p>A very short description.<br>32 mins · Febuary 12</p></div>
  </div>
  <div class="rule" style="top:164px"></div>

  <h2 class="shelf-name" style="top:170px">Matthew 12</h2>
  <div class="shelf" style="top:183px">
    <div class="sermon"><div class="thumb">PIC<i>+ ♥</i></div><h5>TITLE</h5><p>A very short description.<br>32 mins · Febuary 12</p></div>
    <div class="sermon"><div class="thumb">PIC<i>+ ♥</i></div><h5>TITLE</h5><p>A very short description.<br>32 mins · Febuary 12</p></div>
    <div class="sermon"><div class="thumb">PIC<i>+ ♥</i></div><h5>TITLE</h5><p>A very short description.<br>32 mins · Febuary 12</p></div>
    <div class="sermon"><div class="thumb">PIC<i>+ ♥</i></div><h5>TITLE</h5><p>A very short description.<br>32 mins · Febuary 12</p></div>
    <div class="sermon"><div class="thumb">PIC<i>+ ♥</i></div><h5>TITLE</h5><p>A very short description.<br>32 mins · Febuary 12</p></div>
    <div class="sermon"><div class="thumb">PIC<i>+ ♥</i></div><h5>TITLE</h5><p>A very short description.<br>32 mins · Febuary 12</p></div>
  </div>
  <div class="rule" style="top:254px"></div>

  <h2 class="shelf-name" style="top:261px">Funeral</h2>
  <div class="shelf" style="top:274px">
    <div class="sermon"><div class="thumb">PIC<i>+ ♥</i></div><h5>TITLE</h5><p>A very short description.<br>32 mins · Febuary 12</p></div>
    <div class="sermon"><div class="thumb">PIC<i>+ ♥</i></div><h5>TITLE</h5><p>A very short description.<br>32 mins · Febuary 12</p></div>
    <div class="sermon"><div class="thumb">PIC<i>+ ♥</i></div><h5>TITLE</h5><p>A very short description.<br>32 mins · Febuary 12</p></div>
    <div class="sermon"><div class="thumb">PIC<i>+ ♥</i></div><h5>TITLE</h5><p>A very short description.<br>32 mins · Febuary 12</p></div>
    <div class="sermon"><div class="thumb">PIC<i>+ ♥</i></div><h5>TITLE</h5><p>A very short description.<br>32 mins · Febuary 12</p></div>
    <div class="sermon"><div class="thumb">PIC<i>+ ♥</i></div><h5>TITLE</h5><p>A very short description.<br>32 mins · Febuary 12</p></div>
  </div>

  <footer class="site-footer">
    <div class="foot">
      <div class="col"><h4>WHO WE ARE</h4><a>About us</a><a>Ministries</a><a>Events</a></div>
      <div class="col c2"><h4>INFO</h4><a>Careers</a><a>Community</a><a>Blog</a><a>Press</a></div>
      <div class="col c3"><h4>HELP</h4><a>Contact us</a><a>FAQ</a><a>Legal &amp; Privacy</a></div>
      <div class="col c4"><h4>FIND US AT</h4><p>(555) 014-2290<br>Maple Ridge Dr, Eastfield, North<br>Carolina(NC), 27410</p><h4 class="write">WRITE TO US</h4><a class="mail">graceharbor@example.org</a><div class="social"><span></span><span></span><span></span><span></span></div></div>
      <p class="copy">© 2021 Cornerstone. All Rights Reserved. <a>Privacy Policy</a></p>
    </div>
  </footer>
</section>

<p class="abs note">Visit the link in the<br>description to view the<br><b>Interactive Prototype</b><br><b>of the Website</b></p>

</body>
</html>
```